Business Card Design

We would like to re-design our business cards. Our Company - Qwinrel Turbochargers, rebuilds turbochargers and sells replacement parts. Our website is: http://www.qwinrelturbochargers-example.com
We just had our logo changed. I will attach the file. Looking for fresh new/modern business card. We like the colors red, black, white and silver. Black background looks attractive, but not a requirement. The final design should communicate reasonable/competitive prices, top quality and reliability of our products.
Updates
Project Deadline Extended
Reason: Need to finalize the info on the card. Currently working on changing address and email info. Want to make sure it is the correct one before accepting the final design. Unless, this is something that can be changed at a later time..??
Industry/Entity Type
Business
Contact Information for Business Card
QWINREL TURBOCHARGERS, LLC
20473 Harwick Lane NE
Massillon, OH 44647
Tel: +1-555-214-7390
Fax: +1-555-267-1842
info@QwinrelTurbochargers-example.com
Our current business card had the following highlights:
*We rebuild all Turbocharges for Automotive, Diesel and Industrial
*Precision Balancing and in-house turbocharger needs
*All Turbocharger replacement parts are made in USA / U.K.
Look and feel
Each slider illustrates characteristics of the customer's brand and the style your logo design should communicate.

```html
<!DOCTYPE html>
<html lang="en">
<head>
<meta charset="utf-8">
<title>Qwinrel Turbochargers – Business Card</title>
<link href="https://fonts.googleapis.com/css2?family=Raleway:wght@400;500&display=swap" rel="stylesheet">
<style>
  :root {
    --backdrop: #1a1a1b;
    --card: #333438;
    --card-edge: #2a2b2e;
    --brand-red: #e8232a;
    --text-light: #d9d9db;
    --text-muted: #b9babd;
  }
  html, body {
    margin: 0;
    padding: 0;
    width: 1200px;
    height: 900px;
    overflow: hidden;
    background: var(--backdrop);
    font-family: "Raleway", sans-serif;
  }
  .stage {
    position: relative;
    width: 1200px;
    height: 900px;
  }
  .card {
    position: absolute;
    left: 328px;
    width: 545px;
    height: 318px;
    background: var(--card);
    border-radius: 18px;
    box-shadow: 0 2px 0 var(--card-edge);
  }
  .card--front { top: 117px; }
  .card--back  { top: 487px; height: 316px; }

  .brand {
    position: absolute;
    display: flex;
    align-items: center;
    gap: 12px;
    color: var(--brand-red);
    font-weight: 500;
    white-space: nowrap;
  }
  .brand__dot {
    width: 22px;
    height: 22px;
    border-radius: 50%;
    background: var(--brand-red);
    flex: none;
  }
  .card--front .brand {
    left: 48px;
    top: 138px;
    font-size: 38px;
    letter-spacing: 0.5px;
  }
  .card--back .brand {
    left: 0;
    right: 0;
    top: 140px;
    justify-content: center;
    font-size: 32px;
  }

  .contact {
    position: absolute;
    left: 283px;
    top: 113px;
  }
  .contact__name {
    margin: 0;
    color: var(--brand-red);
    font-size: 24px;
    font-weight: 400;
    line-height: 1.1;
  }
  .contact__role {
    margin: 2px 0 0;
    color: var(--text-muted);
    font-size: 16px;
    line-height: 1.2;
  }
  .contact__lines {
    margin: 20px 0 0 4px;
    color: var(--text-light);
    font-size: 14.5px;
    line-height: 1.3;
  }
  .contact__lines p { margin: 0; }
</style>
</head>
<body>
<main class="stage">
  <section class="card card--front" aria-label="Business card front">
    <div class="brand"><span class="brand__dot"></span>Qwinrel</div>
    <div class="contact">
      <h1 class="contact__name">Dara Menlow</h1>
      <p class="contact__role">Managing Director</p>
      <div class="contact__lines">
        <p>info@qwinrel-example.com</p>
        <p>044-555 218 604</p>
      </div>
    </div>
  </section>

  <section class="card card--back" aria-label="Business card back">
    <div class="brand"><span class="brand__dot"></span>Qwinrel Turbochargers</div>
  </section>
</main>
</body>
</html>
```